Chimney Service company needs new business card design

We need a updated business card with our new logo added. We provide a full range of chimney services throughout Vermont and New Hampshire. The business card will be one sided and color. Attached is our current business card another document showing all the information we would like on the card.
We dont like a lot of flashy colors.... here is a link to our website to get an idea of our branding www.flueguardianvt.example

Target Market(s)

homeowners

Industry/Entity Type

Business

Contact Information for Business Card

See attached sheet for content.

Font styles to use
Serif
Sans Serif

Requirements
Must have
• all information provided on separate sheet
Should not have
• Additional information that may clogg up design

```html
<!DOCTYPE html>
<html lang="en">
<head>
<meta charset="utf-8">
<title>Flue Guardian — Business Card</title>
<link rel="stylesheet" href="https://fonts.googleapis.com/css2?family=Cinzel:wght@400&family=Open+Sans:wght@400&display=swap">
<style>
  :root {
    --canvas: #e9e7e3;
    --card-light: #fbfbfa;
    --card-dark: #2e2e2e;
    --card-dark-edge: #1d1d1d;
    --ink: #3a3a3a;
    --ink-soft: #6a6a6a;
    --accent: #a8323a;
    --text-on-dark: #f1f1f1;
    --mark-faint: rgba(255,255,255,0.06);
  }
  * { margin: 0; padding: 0; box-sizing: border-box; }
  html, body { width: 1200px; height: 1022px; overflow: hidden; }
  body {
    background: var(--canvas);
    display: flex;
    flex-direction: column;
    align-items: center;
    justify-content: center;
    gap: 70px;
  }
  .card {
    width: 560px;
    height: 320px;
    position: relative;
    box-shadow: 0 6px 18px rgba(0,0,0,0.18);
  }
  /* Front */
  .card-front { background: var(--card-light); }
  .brand {
    position: absolute;
    left: 48px;
    top: 62px;
    display: flex;
    align-items: center;
    gap: 22px;
  }
  .brand-square {
    width: 92px;
    height: 92px;
    border: 7px solid var(--ink);
  }
  .brand-text { display: flex; flex-direction: column; }
  .brand-name {
    font-family: "Cinzel", serif;
    font-size: 34px;
    color: var(--ink);
    letter-spacing: 1px;
    padding-bottom: 6px;
    border-bottom: 2px solid var(--ink);
  }
  .brand-since {
    font-family: "Cinzel", serif;
    font-size: 13px;
    color: var(--ink-soft);
    letter-spacing: 2px;
    margin-top: 6px;
    align-self: center;
  }
  .contact {
    position: absolute;
    right: 42px;
    bottom: 38px;
    list-style: none;
    font-family: "Open Sans", sans-serif;
    font-size: 17px;
    color: var(--ink);
  }
  .contact li {
    display: flex;
    align-items: center;
    gap: 12px;
    line-height: 30px;
  }
  .contact svg { width: 20px; height: 20px; flex: none; }

  /* Back */
  .card-back {
    background: linear-gradient(135deg, #3a3a3a 0%, var(--card-dark) 50%, var(--card-dark-edge) 100%);
    overflow: hidden;
  }
  .back-mark {
    position: absolute;
    left: 60px;
    top: 60px;
    width: 200px;
    height: 200px;
    background: var(--mark-faint);
  }
  .services {
    position: absolute;
    right: 40px;
    top: 50%;
    transform: translateY(-50%);
    list-style: none;
    font-family: "Cinzel", serif;
    font-size: 17px;
    color: var(--text-on-dark);
    letter-spacing: 0.5px;
  }
  .services li { line-height: 34px; }
  .services li::before {
    content: "";
    display: inline-block;
    width: 7px;
    height: 7px;
    border-radius: 50%;
    background: var(--text-on-dark);
    margin-right: 12px;
    vertical-align: middle;
  }
</style>
</head>
<body>
  <section class="card card-front" aria-label="Card front">
    <div class="brand">
      <div class="brand-square"></div>
      <div class="brand-text">
        <span class="brand-name">Flue Guardian</span>
        <span class="brand-since">INC 1989</span>
      </div>
    </div>
    <ul class="contact">
      <li>
        <svg viewBox="0 0 20 20" aria-hidden="true"><circle cx="10" cy="10" r="10" fill="var(--accent)"/><path d="M7 5.5l1.8 2.4-1 1.2c.6 1.3 1.6 2.3 2.9 2.9l1.2-1 2.4 1.8-.9 1.7c-3.9-.3-7.3-3.7-7.6-7.6z" fill="#fff"/></svg>
        802-555-0147
      </li>
      <li>
        <svg viewBox="0 0 20 20" aria-hidden="true"><circle cx="10" cy="10" r="10" fill="var(--accent)"/><circle cx="10" cy="10" r="5.5" fill="none" stroke="#fff" stroke-width="1.2"/><path d="M4.5 10h11M10 4.5c-2.5 3-2.5 8 0 11M10 4.5c2.5 3 2.5 8 0 11" fill="none" stroke="#fff" stroke-width="1"/></svg>
        info@flueguardianvt.example
      </li>
      <li>
        <svg viewBox="0 0 20 20" aria-hidden="true"><circle cx="10" cy="10" r="10" fill="var(--accent)"/><rect x="5" y="6.5" width="10" height="7" fill="none" stroke="#fff" stroke-width="1.2"/><path d="M5 6.5l5 4 5-4" fill="none" stroke="#fff" stroke-width="1.2"/></svg>
        www.flueguardianvt.example
      </li>
    </ul>
  </section>

  <section class="card card-back" aria-label="Card back">
    <div class="back-mark"></div>
    <ul class="services">
      <li>Full Masonry Services</li>
      <li>Historic Chimney Restoration</li>
      <li>Stainless Steel Liners</li>
      <li>HFSA Certified Chimney Sweep</li>
      <li>Fully Insured • Free Estimates</li>
    </ul>
  </section>
</body>
</html>
```